RM Installations Web Site Design

Need a basic site to show clients a little about what we do. We are a custom audio video company in the high-end residential market. Need a few basic but professional pages to show past projects and products we sell. No e-commerce. Should include my new logo from MarkBazaar.

Industry/Entity Type

Residential

Number of Pages Required

2 page

Font styles to use
Serif
Sans Serif

Colors
f78f20

Requirements
Must have
• Company Logo, Send feedback page
Nice to have
• I have no ideas about design, but I do know what I like and dislike when I see it.

```html
<!DOCTYPE html>
<html lang="en">
<head>
<meta charset="utf-8">
<title>RM Installations</title>
<link href="https://fonts.googleapis.com/css2?family=Roboto:wght@300;400;500&family=Open+Sans:wght@400;600&display=swap" rel="stylesheet">
<style>
:root{
  --orange:#f08a1f;
  --orange-text:#e4822a;
  --ink:#222;
  --muted:#888;
  --nav:#666;
  --panel:#f3f3f3;
  --social:#666;
  --social-line:#777;
  --footer:#333;
  --footer-text:#aaa;
  --white:#fff;
}
*{box-sizing:border-box;margin:0;padding:0}
html,body{width:969px;height:1200px;overflow:hidden;background:var(--white)}
body{position:relative;font-family:"Roboto",sans-serif;color:var(--ink)}
.abs{position:absolute}

.site-header{left:0;top:0;width:969px;height:80px;background:var(--white)}
.brand{left:80px;top:26px;display:flex;align-items:center;gap:8px;font-family:"Roboto",sans-serif;font-weight:400;font-size:17px;color:var(--ink)}
.brand-mark{width:22px;height:22px;background:var(--orange)}
.main-nav{right:82px;top:30px;display:flex;gap:31px;font-size:11px;color:var(--nav)}
.main-nav .active{color:var(--orange)}

.hero{left:0;top:80px;width:969px;height:352px;background:radial-gradient(ellipse at 50% 85%,#4a3a2a 0%,#1a1414 45%,#050505 100%)}
.hero-arrow{top:160px;width:22px;height:32px}
.hero-arrow.prev{left:2px}
.hero-arrow.next{right:0;background:rgba(255,255,255,.25)}

.welcome{left:0;top:432px;width:969px;height:166px;background:var(--orange);color:var(--white);text-align:center}
.welcome h1{font-weight:400;font-size:20px;margin-top:33px}
.welcome p{font-family:"Roboto",sans-serif;font-size:9.6px;line-height:16.6px;width:700px;margin:9px auto 0}

.services-title{left:0;top:630px;width:969px;text-align:center;font-weight:400;font-size:23px;color:var(--orange-text)}
.service{top:672px;width:181px;text-align:center}
.service .photo{height:117px}
.service h3{font-weight:400;font-size:13.5px;color:var(--orange-text);margin-top:9px}
.svc-arrow{top:730px;width:14px;height:24px}

.showcase{left:0;top:860px;width:969px;height:174px;background:var(--panel)}
.showcase h2{top:23px;font-weight:400;font-size:15.5px;color:var(--orange-text)}
.card{top:48px;width:391px;height:98px;background:var(--white);border:1px solid #d8d8d8}
.card .photo{left:4px;top:4px;width:113px;height:89px}
.card h4{left:131px;top:18px;font-weight:400;font-size:11.5px;color:var(--ink)}
.card p{left:131px;top:38px;width:250px;font-family:"Open Sans",sans-serif;font-size:7.6px;line-height:13px;color:var(--muted)}

.social-bar{left:0;top:1034px;width:969px;height:62px;background:var(--social)}
.social-links{left:80px;top:0;display:flex;height:62px;border-left:1px solid var(--social-line)}
.social-links span{width:52px;height:62px;border-right:1px solid var(--social-line);display:flex;align-items:center;justify-content:center}
.social-links span:first-child{background:#5a5a5a}
.social-links i{display:block;width:17px;height:17px;background:#bbb;border-radius:3px}
.social-links span:first-child i{background:var(--white)}
.newsletter{left:551px;top:18px;display:flex;align-items:center}
.newsletter label{font-weight:300;font-size:13.5px;color:var(--white);margin-right:11px}
.newsletter .field{width:146px;height:26px;background:var(--white);border-radius:2px 0 0 2px;font-family:"Open Sans",sans-serif;font-size:8px;color:var(--muted);padding:8px 9px}
.newsletter .btn{width:57px;height:26px;background:var(--orange);color:var(--white);font-family:"Open Sans",sans-serif;font-size:9px;line-height:26px;text-align:center;border-radius:0 2px 2px 0}

.site-footer{left:0;top:1096px;width:969px;height:104px;background:var(--footer);text-align:center;font-family:"Open Sans",sans-serif;font-size:9px;color:var(--footer-text)}
.site-footer .links{margin-top:23px}
.site-footer .links b{font-weight:400;color:var(--white)}
.site-footer .sep{margin:0 7px}
.site-footer .info{margin-top:12px}
.site-footer .copy{margin-top:11px}
.site-footer .tag{position:absolute;right:8px;bottom:8px;color:var(--white);font-size:9px}
</style>
</head>
<body>

<header class="site-header abs">
  <div class="brand abs"><span class="brand-mark"></span>RM Installations</div>
  <nav class="main-nav abs"><span class="active">Home</span><span>About us</span><span>Services</span><span>Projects</span><span>Contact us</span></nav>
</header>

<section class="hero abs" role="img" aria-label="Broadcast control room with glowing monitors above a lit mixing console">
  <svg class="hero-arrow prev abs" viewBox="0 0 22 32"><path d="M14 9 L8 16 L14 23" fill="none" stroke="#ccc" stroke-width="1.5"/></svg>
  <svg class="hero-arrow next abs" viewBox="0 0 22 32"><path d="M8 9 L14 16 L8 23" fill="none" stroke="#fff" stroke-width="1.5"/></svg>
</section>

<section class="welcome abs">
  <h1>Welcome to RM Installations</h1>
  <p>Donec posuere elementum erat, at varius lacus ultricies a. Nulla facilisi. Fusce ultrices imperdiet lacus at tincidunt. Sed feugiat sodales quam a laoreet. Nullam at ornare urna. Fusce maximus fermentum neque, nec dictum ipsum egestas vitae. Praesent neque neque, vestibulum non orci vitae, pulvinar lobortis orci. Phasellus maximus auctor dui, eu lobortis ipsum accumsan quis. Sed vestibulum congue odio at volutpat. Pellentesque habitant morbi tristique senectus et netus et malesuada fames ac turpis egestas. Curabitur sed mauris eleifend, feugiat ante vitae, hendrerit nisl.</p>
</section>

<h2 class="services-title abs">Our Services</h2>
<svg class="svc-arrow abs" style="left:80px" viewBox="0 0 14 24"><path d="M11 3 L3 12 L11 21" fill="none" stroke="#bbb" stroke-width="2"/></svg>
<svg class="svc-arrow abs" style="left:875px" viewBox="0 0 14 24"><path d="M3 3 L11 12 L3 21" fill="none" stroke="#bbb" stroke-width="2"/></svg>
<div class="service abs" style="left:110px"><div class="photo" role="img" aria-label="Close-up of a loudspeaker" style="background:linear-gradient(90deg,#b8aea4,#6e6660 55%,#2a2a2a)"></div><h3>Distributed Audio</h3></div>
<div class="service abs" style="left:299px"><div class="photo" role="img" aria-label="Tablet showing a video library" style="background:linear-gradient(90deg,#3a3a3a,#1c1c1c 40%,#d8d8d8 60%,#3a3a3a)"></div><h3>Distributed Video</h3></div>
<div class="service abs" style="left:488px"><div class="photo" role="img" aria-label="Technician at a media room control desk" style="background:linear-gradient(180deg,#3c4a6a,#1a1f2c 55%,#6a6a6a)"></div><h3>Media Rooms</h3></div>
<div class="service abs" style="left:676px"><div class="photo" role="img" aria-label="Home cinema with red seats and a screen" style="background:linear-gradient(180deg,#8a6a4a,#b45a30 55%,#6a2a1a)"></div><h3>Residential Cinemas</h3></div>

<section class="showcase abs">
  <h2 class="abs" style="left:80px">Past Projects</h2>
  <h2 class="abs" style="left:495px">Our Products</h2>
  <article class="card abs" style="left:81px">
    <div class="photo abs" role="img" aria-label="Living room with a wall-mounted television" style="background:linear-gradient(180deg,#c23a2a,#e8e0d8 50%,#a05a30)"></div>
    <h4 class="abs">Aenean facilisis tincidunt lectus</h4>
    <p class="abs">Etiam vel massa elementum, bibendum tellus venenatis, feugiat massa. Curabitur venenatis lacinia ornare. Cras sollicitu din cursus dui eu placerat.</p>
  </article>
  <article class="card abs" style="left:496px">
    <div class="photo abs" role="img" aria-label="Outdoor speaker on a stage" style="background:linear-gradient(180deg,#b8cde0,#6a8a5a 40%,#4a4a4e)"></div>
    <h4 class="abs">Suspendisse vehicula odio eros</h4>
    <p class="abs">Etiam vel massa elementum, bibendum tellus venenatis, feugiat massa. Curabitur venenatis lacinia ornare. Cras sollicitu din cursus dui eu placerat.</p>
  </article>
</section>

<section class="social-bar abs">
  <div class="social-links abs">
    <span><i></i></span><span><i></i></span><span><i></i></span><span><i></i></span>
    <span><svg width="21" height="15" viewBox="0 0 21 15"><rect x="1" y="1" width="19" height="13" rx="1.5" fill="#bbb"/><path d="M1.5 2 L10.5 9 L19.5 2" fill="none" stroke="#666" stroke-width="1.5"/></svg></span>
  </div>
  <div class="newsletter abs"><label>Newsletter Subscribe</label><div class="field">Email Address</div><div class="btn">Subscribe</div></div>
</section>

<footer class="site-footer abs">
  <div class="links"><b>Home</b><span class="sep">|</span>About us<span class="sep">|</span>Services<span class="sep">|</span>Projects<span class="sep">|</span>Contact us</div>
  <div class="info">License: 0204417-B2<span class="sep">|</span>PH:555-010-4821<span class="sep">|</span>hello@rminstallations.example</div>
  <div class="copy">Copyright ©&nbsp; 2015&nbsp; RM Installations LLC.&nbsp;&nbsp; All rights reserved | Privacy Policy</div>
  <span class="tag">M2</span>
</footer>

</body>
</html>
```